Nutritional & Gastrointestinal Health Consulting Service-Website design

We need a website design for a new health consulting service called "Bright Vale" based in Perth, Australia.

We will be providing consulting services in the areas of:
1) Nutrition and Diet
2) Gastrointestinal Health (which means stomach & digestive system related health)

These consulting services will be provided by an Accredited Dietitian and a Paediatric Gastroenterologist.

We are open to creative ideas in terms of design, layout, fonts and colours. We also would love to see images of nature in the backdrop with families (adults with kids) having a good time, fresh fruits and vegetables displayed in a farmer's market or supermarket. 2 or 3 images should be sufficient. We would also definitely want our logo somewhere in the main page of website. The logo file is also attached. Please have a look at a website's design that we really liked. We would love to see designs inspired by that style. The website details are in the in the "nice to have priorities" section of this project brief.

We also would be looking at website designers with software coding skills so that if we like the design we can go ahead with the next step of coding.

The website design should communicate the purpose of the website and at the same time be simple, elegant and unique/eye-catching.

We look forward to receiving creative ideas for our website from you all. Good luck!

More details have been added to our project- for example: Logo, fonts style, must haves etc etc. Please view the updated project brief. Looking forward to receiving your fantastic ideas for our website. Thanking you

Hi, I have updated the colour preference. Will add the content preferences tomorrow. thanks

Hello all, I have now added a LOT more content to what we want in our website. It is very much in detail, so please carefully have a read through the entire project brief. If you have any questions write back to me and I will try to respond as quickly as I can. Last few days were busy so couldn't respond quickly to all of you who had send me designs/queries/questions. Thank you for your patience. I look forward to receiving fantastic designs from you all. Good Luck :-)

Target Market(s)

Adults based in western speaking countries aged 18 to 60 years

Industry/Entity Type

Software

Font styles to use
Sans Serif
Script

Colors
faa54b
acd036

Requirements
Must have
• The website must have the MAIN logo file attached. I have attached 3 files: 1) MAIN logo; 2) supplementary logo A ; 3) supplementary logo B

I have selected 2 colours from the colour scheme (see below)-(as the colour of our logo is that).
However we would also like to see LIGHT CHOCOLATE BROWN or CHOCOLATE BROWN colour used as the background colour of the website
Preferred WEBSITE CONTENT:
1) HOME PAGE:
Content required=
--Company Logo
--Dr Dorian Pelham
Paediatric Gastroenterologist & Hepatologist
-Marla Pelham.
Dietitian & Nutritionist
--Website Menu (either listed horizontally or vertically):
Once clicked on each name:

Under each of the Website Menu items we want the following Headings to be added

2) ABOUT US page:
Sub-heading under this: Qualification, Skills, Special Interest

3) SERVICES
DORIAN'S PAGE: Individual Consultation, Endoscopy procedures
Individual Consultation, Group Based Services, Food Diary, Food & Symptom Diary

4) FEES & REBATE: Content as below:
Please Note: Payment of full fees is required at the time of consultation and procedures. 48 hours notice is required for cancellation of appointments/non-attendance. Failure to provide this may result in a fee being incurred. Please call reception to find out the amount of fee charged for cancellation of appointments/non-attendance.
headings are:
Paediatric Gastroenterology:
Dorian's pge
Individual Consultation - Initial (upto 30 mins):
Review Consultation (upto 15 mins):
Endoscopy procedures - No Gap fees charged. Fees will be billed directly to Vitacover. If any queries, please contact reception.

marla's pge
sub heading:
Individual Consultation - Initial (upto 45 mins):
Individual Consultation - Review (upto 30 mins):

Concession-Individual Consultation -Initial (upto 45 mins):
Concession-Individual Consultation - Review (upto 30 mins):
Please Note: Concession applies for health care card holders & pensioners

Group Based Services: Pricing subject to the type of service provided. Please contact us for an obligation free quote.
Education Topics Include:
- Paediatric Nutrition (Introducing Solids, Fussy Eating, Healthy Eating)
- Pregnancy Nutrition, Gestational Diabetes, Breastfeeding/Lactation Nutrition
- Healthy Eating, Supermarket Shopping Tips, Nutrition Label Reading Tips, Healthier
sub heading under nutrition & diet:
-Vitacover:
--A rebate of $52.95 is available from Vitacover if an EPC ( Enhanced Primary Care)/Chronic Disease Management (CDM) plan is issued by your GP.
--All mandatory paperwork needs to be available at the time of making your appointment for your eligibility.
-Private Health Fund:
--Most private health funds provide rebate on dietetic appointments. However the rebate amount depends on your level of cover. Thus, please contact your health fund to determine your entitled rebate.
-RSB: Approved provider for RSB services

6) FOR DOCTORS: Bright Vale Paediatric Gastroenterologist Referral Form
Bright Vale Dietitian Referral form
7) LOCATIONS & CONTACT

Paediatric Gastroenterology & Hepatology Service
Suite 46
Holy Lantern Bramcote Medical Centre
17 Colin Ferris Pde,
MURDOCH, WA 6150
P: (08) 9422 5061
F: (08) 9422 3094

Nutrition & Diet Service
Suite 46
17 Colin Ferris Pde,
MURDOCH, WA 6150
P: (08) 9422 5061
F: (08) 9422 3094

Tolland Medical Centre
58-60 Karrigan Parkway,
MANDURAH, WA 6210
P: (08) 9647 2283
F: (08) 96724419
www.tmcexample.com.au

This page should have a webform that has following titles:
-Your Name
-Your Email
-Your Phone
-Message

8) NEWS & BLOG
Nice to have
• We liked the design style of the websites below:
https://www.vendoraplex.example/

http://qoravelt.example/

But feel free to use your creativity too
Should not have
• Please do not use any body building or muscle building images

```html
<!DOCTYPE html>
<html lang="en">
<head>
<meta charset="utf-8">
<title>Bright Vale — Health Consulting Services</title>
<link rel="stylesheet" href="https://fonts.googleapis.com/css2?family=Raleway:wght@500;700;800;900&family=Open+Sans:wght@400;600;700&display=swap">
<style>
  :root {
    --brown: #4a2c28;
    --brown-dark: #3d2420;
    --orange: #faa54b;
    --green: #acd036;
    --red: #c9302c;
    --white: #ffffff;
    --text-dark: #2b2b2b;
  }
  * { margin: 0; padding: 0; box-sizing: border-box; }
  html, body { width: 1048px; height: 1200px; overflow: hidden; }
  body { font-family: "Open Sans", sans-serif; background: var(--brown); position: relative; }

  .site-header { position: absolute; left: 0; top: 0; width: 1048px; height: 79px; background: var(--brown); border-bottom: 3px solid var(--red); }
  .brand { position: absolute; left: 58px; top: 22px; display: flex; align-items: center; gap: 10px; }
  .brand-dot { width: 30px; height: 30px; border-radius: 50%; background: var(--orange); }
  .brand-name { font-family: "Raleway", sans-serif; font-weight: 800; font-size: 24px; color: var(--orange); letter-spacing: 0.5px; }
  .main-nav { position: absolute; left: 267px; top: 0; height: 79px; display: flex; }
  .main-nav a { display: flex; flex-direction: column; align-items: center; justify-content: center; height: 79px; padding: 0 14px; color: var(--white); text-decoration: none; font-family: "Open Sans", sans-serif; font-weight: 700; font-size: 10.5px; letter-spacing: 0.2px; border-right: 1px solid rgba(255,255,255,0.07); }
  .main-nav a .nav-icon { width: 8px; height: 8px; border: 1.5px solid rgba(255,255,255,0.55); border-radius: 2px; margin-bottom: 10px; }
  .main-nav a.is-active { background: var(--orange); width: 57px; padding: 0; }

  .hero { position: absolute; left: 0; top: 82px; width: 1048px; height: 410px; background: linear-gradient(180deg, #5aa0d8 0%, #9fcbe8 45%, #6f9a3a 62%, #a6c146 85%, #8aa23c 100%); }
  .hero-kicker { position: absolute; left: 0; width: 1048px; top: 128px; text-align: center; font-family: "Raleway", sans-serif; font-weight: 800; font-size: 24px; color: var(--green); letter-spacing: -0.5px; }
  .hero-title { position: absolute; left: 0; width: 1048px; top: 152px; text-align: center; font-family: "Raleway", sans-serif; font-weight: 900; font-size: 64px; color: var(--orange); letter-spacing: -1px; }
  .hero-rule { position: absolute; left: 138px; top: 224px; width: 785px; height: 2px; background: rgba(250,200,140,0.6); }
  .hero-lead { position: absolute; left: 0; width: 1048px; top: 245px; text-align: center; font-size: 12.5px; color: var(--text-dark); }
  .hero-button { position: absolute; left: 478px; top: 272px; width: 104px; height: 35px; background: var(--green); color: var(--brown-dark); font-weight: 700; font-size: 11px; letter-spacing: 1px; display: flex; align-items: center; justify-content: center; }

  .services { position: absolute; left: 0; top: 494px; width: 1048px; height: 404px; background: var(--brown); border-top: 2px solid var(--white); }
  .service { position: absolute; top: 0; width: 300px; text-align: center; }
  .service-icon { position: absolute; left: 120px; top: 59px; width: 60px; height: 78px; display: flex; justify-content: center; }
  .service-title { position: absolute; left: 0; width: 300px; top: 154px; font-family: "Raleway", sans-serif; font-weight: 500; font-size: 15px; color: var(--orange); }
  .service-sub { position: absolute; left: 0; width: 300px; top: 178px; font-size: 9.5px; letter-spacing: 1px; color: var(--green); }
  .service-divider { position: absolute; left: 137px; top: 208px; width: 26px; height: 1px; background: rgba(255,255,255,0.6); }
  .service-text { position: absolute; left: 0; width: 300px; top: 226px; font-size: 10.5px; line-height: 18px; color: var(--white); }
  .service-link { position: absolute; left: 0; width: 300px; top: 280px; font-size: 10.5px; color: var(--orange); }

  .site-footer { position: absolute; left: 0; top: 898px; width: 1048px; height: 282px; background: var(--orange); border-top: 3px solid var(--green); }
  .footer-brand { position: absolute; left: 58px; top: 70px; display: flex; align-items: center; gap: 8px; }
  .footer-brand .brand-dot { background: var(--white); width: 24px; height: 24px; }
  .footer-brand .brand-name { color: var(--white); font-size: 22px; }
  .footer-col { position: absolute; top: 63px; }
  .footer-col h3 { font-family: "Raleway", sans-serif; font-weight: 500; font-size: 19px; color: var(--white); margin-bottom: 22px; }
  .footer-col p { width: 300px; font-size: 10.5px; line-height: 18px; color: var(--white); margin-top: 6px; }
  .footer-col ul { list-style: none; padding-left: 5px; }
  .footer-col li { font-size: 10.5px; color: var(--white); height: 25px; }
  .footer-bar { position: absolute; left: 0; top: 1180px; width: 1048px; height: 20px; background: var(--brown-dark); }
</style>
</head>
<body>
  <header class="site-header">
    <div class="brand"><span class="brand-dot"></span><span class="brand-name">Bright Vale</span></div>
    <nav class="main-nav">
      <a class="is-active"><span class="nav-icon"></span>HOME</a>
      <a><span class="nav-icon"></span>ABOUT US</a>
      <a><span class="nav-icon"></span>NUTRITION &amp; DIET</a>
      <a><span class="nav-icon"></span>PAEDIATRIC GASTROENTEROLOGY</a>
      <a><span class="nav-icon"></span>FEES &amp; REBATE</a>
      <a><span class="nav-icon"></span>DOCTORS</a>
      <a><span class="nav-icon"></span>CONTACTS</a>
    </nav>
  </header>

  <section class="hero" role="img" aria-label="Photo of a smiling family with a child on a father's shoulders in a sunny green meadow">
    <div class="hero-kicker">HEALTH CONSULTING SERVICES</div>
    <div class="hero-title">HEALTH FOR EVERYONE!</div>
    <div class="hero-rule"></div>
    <p class="hero-lead">We need a website design for a new health consulting service called "Bright Vale" based in Perth, Australia.</p>
    <div class="hero-button">READ MORE</div>
  </section>

  <section class="services">
    <article class="service" style="left:57px">
      <div class="service-icon"><svg role="img" aria-label="Fruit illustration" width="52" height="78" viewBox="0 0 52 78"><ellipse cx="26" cy="46" rx="24" ry="30" fill="#faa54b"/></svg></div>
      <h2 class="service-title">Nutrition and Diet</h2>
      <div class="service-sub">INDIVIDUAL CONSULTATION</div>
      <div class="service-divider"></div>
      <p class="service-text">These consulting services will be provided by an Accredited Dietitian and a Paediatric Gastroenterologist.</p>
      <div class="service-link">read more ➔</div>
    </article>
    <article class="service" style="left:380px">
      <div class="service-icon"><svg role="img" aria-label="Digestive system illustration" width="40" height="78" viewBox="0 0 40 78"><rect x="2" y="6" width="36" height="68" rx="18" fill="#faa54b"/></svg></div>
      <h2 class="service-title">Gastrointestinal Health</h2>
      <div class="service-sub">GASTROINTESTINAL AND LIVER DISORDERS</div>
      <div class="service-divider"></div>
      <p class="service-text">These consulting services will be provided by an Accredited Dietitian and a Paediatric Gastroenterologist.</p>
      <div class="service-link">read more ➔</div>
    </article>
    <article class="service" style="left:703px">
      <div class="service-icon"><svg width="46" height="72" viewBox="0 0 46 72"><path d="M23 2C12 2 5 10 5 20c0 13 18 34 18 34s18-21 18-34C41 10 34 2 23 2z" fill="#faa54b"/><circle cx="23" cy="20" r="7" fill="#4a2c28"/><ellipse cx="23" cy="60" rx="19" ry="7" fill="none" stroke="#faa54b" stroke-width="4"/></svg></div>
      <h2 class="service-title">Locations &amp; Contact</h2>
      <div class="service-sub">PAEDIATRIC GASTROENTEROLOGY SERVICE</div>
      <div class="service-divider"></div>
      <p class="service-text">These consulting services will be provided by an Accredited Dietitian and a Paediatric Gastroenterologist.</p>
      <div class="service-link">read more ➔</div>
    </article>
  </section>

  <footer class="site-footer">
    <div class="footer-brand"><span class="brand-dot"></span><span class="brand-name">Bright Vale</span></div>
    <div class="footer-col" style="left:219px">
      <h3>About us</h3>
      <p>We would like to see the website design that uses the colour green and yellowish orange (as the colour of our logo is that). We are open to creative ideas in terms of design, layout, fonts and colours. We also would love to see images of nature in the backdrop with families (adults with kids).</p>
    </div>
    <div class="footer-col" style="left:542px">
      <h3>Site</h3>
      <ul><li>Home</li><li>About us</li><li>Services</li><li>News</li><li>Contact Us</li></ul>
    </div>
    <div class="footer-col" style="left:704px">
      <h3>Support</h3>
      <ul><li>FAQ's</li><li>Disclaimer</li><li>Support</li><li>Products</li><li>Help</li></ul>
    </div>
    <div class="footer-col" style="left:865px">
      <h3>Network</h3>
      <ul><li>Pinvale</li><li>Chirpline</li><li>Reelcast</li><li>Snapleaf</li><li>Workring</li></ul>
    </div>
  </footer>
  <div class="footer-bar"></div>
</body>
</html>
```